Product Description Graphic

We are designing a new product and need a better graphic to describe it.

We are not worried about names of the modules yet but want to be descriptive of capabilities. Right now "Present & CMA" should really be "Presentations & CMA".

I overall like the shape of the triangle and the arrow for Contacts but this is a very unsophisticated graphic done by a non-designer. Also need to better show that each block of capabilites will also have paywall capabilities.

Target Market(s)

Real Estate Brokerage Firms and Real Estate Agents

Industry/Entity Type

Real Estate

Colors

Designer to choose colors to be used in the design.

Requirements
Must have
• Sophisticated design. Paywall description embedded.

```html
<!DOCTYPE html>
<html lang="en">
<head>
<meta charset="utf-8">
<title>Product Capabilities Diagram</title>
<link href="https://fonts.googleapis.com/css2?family=Nunito+Sans:wght@700;800;900&display=swap" rel="stylesheet">
<style>
  :root {
    --canvas: #ffffff;
    --ring-bg: #e1e2e2;
    --hatch-line: #5e3550;
    --email-outer: #9bbebe;
    --email-inner: #7a9b95;
    --present-outer: #a9b8be;
    --present-inner: #868d8b;
    --mobile-outer: #8a9fa3;
    --mobile-inner: #6c7674;
    --web-outer: #5f8e89;
    --web-inner: #4f6e69;
    --contacts: #90a7b1;
    --contacts-outer: #abc4cc;
    --label: #111111;
    --legend-line: #9a9a9a;
  }
  html, body {
    margin: 0;
    padding: 0;
    width: 1200px;
    height: 1200px;
    overflow: hidden;
    background: var(--canvas);
  }
  .diagram {
    display: block;
    width: 1200px;
    height: 1200px;
  }
  .module-label {
    font-family: "Nunito Sans", Arial, sans-serif;
    font-weight: 900;
    font-size: 29px;
    letter-spacing: 0.5px;
    fill: var(--label);
  }
  .core-label {
    font-family: "Nunito Sans", Arial, sans-serif;
    font-weight: 800;
    font-size: 22px;
    fill: #ffffff;
  }
  .legend-label {
    font-family: "Nunito Sans", Arial, sans-serif;
    font-weight: 800;
    font-size: 16px;
    fill: var(--label);
  }
</style>
</head>
<body>
<svg class="diagram" viewBox="0 0 1200 1200" xmlns="http://www.w3.org/2000/svg">
  <defs>
    <pattern id="paywall-hatch" patternUnits="userSpaceOnUse" width="19" height="19" patternTransform="rotate(-45 600 600)">
      <line x1="0" y1="0" x2="0" y2="19" stroke="var(--hatch-line)" stroke-width="1.3"/>
    </pattern>
    <path id="path-email" d="M306.4 678.7 A304 304 0 0 1 531.6 303.9" fill="none"/>
    <path id="path-present" d="M678.7 306.4 A304 304 0 0 1 893.6 521.3" fill="none"/>
    <path id="path-mobile" d="M788.1 868.7 A328 328 0 0 0 919.6 673.8" fill="none"/>
    <path id="path-web" d="M331.3 788.1 A328 328 0 0 0 662.6 922.0" fill="none"/>
  </defs>

  <!-- base ring -->
  <circle class="ring-base" cx="600" cy="600" r="340" fill="var(--ring-bg)"/>

  <!-- paywall bands -->
  <g class="paywall-band">
    <path class="band-email" d="M384.5 794.0 A290 290 0 0 1 600 310 L600 454 A146 146 0 0 0 491.5 697.7 Z" fill="var(--email-outer)"/>
    <path d="M384.5 794.0 A290 290 0 0 1 600 310 L600 454 A146 146 0 0 0 491.5 697.7 Z" fill="url(#paywall-hatch)"/>
    <path class="band-present" d="M600 310 A290 290 0 0 1 890 600 L746 600 A146 146 0 0 0 600 454 Z" fill="var(--present-outer)"/>
    <path d="M600 310 A290 290 0 0 1 890 600 L746 600 A146 146 0 0 0 600 454 Z" fill="url(#paywall-hatch)"/>
    <path class="band-mobile" d="M890 600 A290 290 0 0 1 699.2 872.6 L649.9 737.2 A146 146 0 0 0 746 600 Z" fill="var(--mobile-outer)"/>
    <path d="M890 600 A290 290 0 0 1 699.2 872.6 L649.9 737.2 A146 146 0 0 0 746 600 Z" fill="url(#paywall-hatch)"/>
    <path class="band-contacts" d="M699.2 872.6 A290 290 0 0 1 600 890 L600 746 A146 146 0 0 0 649.9 737.2 Z" fill="var(--contacts-outer)"/>
    <path d="M699.2 872.6 A290 290 0 0 1 600 890 L600 746 A146 146 0 0 0 649.9 737.2 Z" fill="url(#paywall-hatch)"/>
    <path class="band-web" d="M600 890 A290 290 0 0 1 384.5 794.0 L491.5 697.7 A146 146 0 0 0 600 746 Z" fill="var(--web-outer)"/>
    <path d="M600 890 A290 290 0 0 1 384.5 794.0 L491.5 697.7 A146 146 0 0 0 600 746 Z" fill="url(#paywall-hatch)"/>
  </g>

  <!-- core capability blocks -->
  <g class="module-core">
    <path class="core-email" d="M420.2 761.9 A242 242 0 0 1 600 358 L600 454 A146 146 0 0 0 491.5 697.7 Z" fill="var(--email-inner)"/>
    <path class="core-present" d="M600 358 A242 242 0 0 1 842 600 L746 600 A146 146 0 0 0 600 454 Z" fill="var(--present-inner)"/>
    <path class="core-mobile" d="M842 600 A242 242 0 0 1 682.8 827.5 L649.9 737.2 A146 146 0 0 0 746 600 Z" fill="var(--mobile-inner)"/>
    <path class="core-web" d="M600 842 A242 242 0 0 1 420.2 761.9 L491.5 697.7 A146 146 0 0 0 600 746 Z" fill="var(--web-inner)"/>
  </g>

  <!-- gap around contacts hub -->
  <circle cx="600" cy="600" r="148" fill="var(--ring-bg)"/>

  <!-- contacts tail -->
  <path class="contacts-tail" d="M682.8 827.5 A242 242 0 0 1 600 842 L600 710 L637.6 703.4 Z" fill="var(--contacts)"/>

  <!-- separators -->
  <g class="separators" stroke="var(--ring-bg)" stroke-width="22" stroke-linecap="butt">
    <line x1="600" y1="478" x2="600" y2="306"/>
    <line x1="722" y1="600" x2="894" y2="600"/>
    <line x1="641.7" y1="714.6" x2="700.6" y2="876.3"/>
    <line x1="600" y1="722" x2="600" y2="894"/>
    <line x1="509.3" y1="681.6" x2="381.5" y2="796.7"/>
  </g>

  <!-- hub -->
  <circle class="contacts-hub" cx="600" cy="600" r="121" fill="var(--contacts)"/>
  <text class="core-label" x="601" y="608" text-anchor="middle">CONTACTS</text>

  <!-- module labels -->
  <text class="module-label"><textPath href="#path-email" startOffset="50%" text-anchor="middle">Email Nateure Print</textPath></text>
  <text class="module-label"><textPath href="#path-present" startOffset="50%" text-anchor="middle">Presentations</textPath></text>
  <text class="module-label"><textPath href="#path-mobile" startOffset="50%" text-anchor="middle">Mobile</textPath></text>
  <text class="module-label"><textPath href="#path-web" startOffset="50%" text-anchor="middle">Websites &amp; Leads</textPath></text>

  <!-- legend -->
  <g class="legend">
    <g stroke="var(--legend-line)" stroke-width="1">
      <line x1="880" y1="970" x2="910" y2="1000"/>
      <line x1="898" y1="970" x2="928" y2="1000"/>
      <line x1="872" y1="992" x2="906" y2="1026"/>
      <line x1="872" y1="1020" x2="878" y2="1026"/>
    </g>
    <text class="legend-label" x="962" y="993">Paywall</text>
    <text class="legend-label" x="962" y="1025">Feature</text>
  </g>
</svg>
</body>
</html>
```